New Interrior Decoration company needs new website

We need a website for our new company specialising in interior decoration to residential and commercial markets.
We supply and install decorative and printed films for office and home decoration such as feature walls.
We would like to keep the design simple and clean.

Target Market(s)

Architects and interior designaers

Industry/Entity Type

It Company

Number of Pages Required

5+ page

Font styles to use
Sans Serif

Requirements
Must have
• Home page,
• Services/products page (split into commercial and residential)
• Gallery (split into commercial and residential)
• contact form and page
Nice to have
• Very clean and minimalistic design.

```html
<!DOCTYPE html>
<html lang="en">
<head>
<meta charset="utf-8">
<title>Northlane Interiors</title>
<link href="https://fonts.googleapis.com/css2?family=Lato:wght@400;700&family=Arimo:wght@400&display=swap" rel="stylesheet">
<style>
:root{
  --blue:#0a5fb8;
  --blue-bright:#1575d6;
  --ink:#1e1e1e;
  --grey-text:#8c8c8c;
  --call-bar:#5e5e5e;
  --footer:#2f2f2f;
  --footer-text:#a9a9a9;
  --white:#ffffff;
  --tab-bg:#ececec;
}
*{margin:0;padding:0;box-sizing:border-box}
html,body{width:1200px;height:2663px;overflow:hidden;background:var(--white)}
body{font-family:"Lato",sans-serif;color:var(--ink);position:relative}
.abs{position:absolute}

/* Hero */
.hero{left:0;top:0;width:1200px;height:677px;overflow:hidden}
.hero-photo{left:0;top:0;width:1200px;height:677px;
  background:linear-gradient(180deg,#eeeeee 0%,#e8e8e8 45%,#d9d4c8 70%,#8a857c 100%)}
.nav{left:0;top:0;width:1200px;height:74px;border-bottom:1px solid #bdbdbd}
.nav a{position:absolute;top:30px;font-size:17px;letter-spacing:.5px;color:#333;text-decoration:none}
.nav a.active{color:var(--blue)}
.nav .underline{position:absolute;left:298px;top:70px;width:82px;height:4px;background:var(--blue)}
.brand{left:322px;top:252px;height:104px;display:flex;align-items:center;gap:20px}
.brand .mark{width:104px;height:104px;background:var(--blue)}
.brand .name{font-weight:700;font-size:58px;line-height:52px;color:#333;letter-spacing:-1px}

/* Call bar */
.call{left:0;top:677px;width:1200px;height:125px;background:var(--call-bar);color:var(--white);
  display:flex;align-items:center;justify-content:center;gap:30px;font-size:42px}
.call .icon{width:76px;height:76px}

/* Headings */
.section-title{width:1200px;left:0;text-align:center;font-size:42px;font-weight:400;color:var(--ink)}
.section-title span{color:var(--blue)}
.btn{background:var(--blue);color:var(--white);font-size:21px;display:flex;align-items:center;justify-content:center;border-radius:3px}

/* About */
.about-text{left:142px;top:918px;width:916px;text-align:center;font-family:"Arimo",sans-serif;font-size:15.5px;line-height:27.5px;color:var(--grey-text)}

/* Services */
.services{left:0;top:1170px;width:1200px;height:536px;background:linear-gradient(90deg,#6f6f6f 0%,#a0a0a0 35%,#d4d4d4 62%,#ece9e5 80%)}
.shelf{left:950px;top:1170px;width:250px;height:536px;background:linear-gradient(180deg,#ebe7e2 0%,#e2ddd6 75%,#c9b9a3 88%,#bda88d 100%)}
.svc-img{left:78px;width:249px;height:165px;border:2px solid #dcdcdc}
.svc-title{left:344px;font-size:19px;font-weight:400;color:var(--ink)}
.svc-text{left:344px;width:570px;font-family:"Arimo",sans-serif;font-size:15px;line-height:25px;color:#5a5a5a}
.read-more{left:344px;font-family:"Arimo",sans-serif;font-size:15px;color:var(--blue);display:flex;align-items:center;gap:4px}

/* Gallery */
.tab{top:1839px;height:40px;font-family:"Arimo",sans-serif;font-size:17px;display:flex;align-items:center;justify-content:center;color:#555}
.tab.active{background:var(--tab-bg);color:var(--blue)}
.gal-img{top:1905px;width:249px;height:176px}

/* Newsletter */
.newsletter{left:0;top:2222px;width:1200px;height:140px;background:linear-gradient(90deg,#0b5eb3,#1a6fc6 50%,#0b5eb3)}
.newsletter h2{position:absolute;left:140px;top:48px;font-weight:400;font-size:39px;color:var(--white)}
.subscribe{left:788px;top:2261px;width:270px;height:61px;background:var(--white);border-radius:3px;color:var(--blue);font-size:21px;display:flex;align-items:center;padding-left:22px;gap:40px}

/* Footer */
.footer{left:0;top:2362px;width:1200px;height:301px;background:var(--footer)}
.foot-head{top:2393px;font-size:15px;font-weight:400;color:var(--blue-bright)}
.foot-list{top:2430px;list-style:none;font-family:"Arimo",sans-serif;font-size:13.5px;color:var(--footer-text)}
.foot-list li{height:27px;display:flex;align-items:center;gap:14px}
.foot-list li::before{content:"";width:8px;height:8px;border-radius:50%;background:var(--blue-bright)}
.contact-row{left:580px;font-family:"Arimo",sans-serif;font-size:13.5px;line-height:24px;color:var(--footer-text);display:flex;gap:16px}
.contact-row svg{flex:none;margin-top:4px}
.foot-brand{left:873px;top:2393px;display:flex;align-items:center;gap:10px}
.foot-brand .mark{width:44px;height:44px;background:var(--blue-bright)}
.foot-brand .name{font-weight:700;font-size:25px;line-height:24px;color:var(--blue-bright)}
.foot-rule{left:900px;top:2464px;width:196px;height:1px;background:#555}
.social{top:2485px;width:40px;height:40px;border-radius:2px}
.copyright{left:0;top:2622px;width:1200px;text-align:center;font-family:"Arimo",sans-serif;font-size:14px;color:#ddd}
.copyright span{color:var(--blue-bright)}
</style>
</head>
<body>

<header class="abs hero">
  <div class="abs hero-photo" role="img" aria-label="Photo of a bright living room with a yellow sofa, rug, coffee table, arc floor lamp and black lounge chair"></div>
  <nav class="abs nav">
    <a class="active" style="left:316px" href="#">HOME</a>
    <a style="left:423px" href="#">ABOUT US</a>
    <a style="left:563px" href="#">SERVICES</a>
    <a style="left:703px" href="#">GALLERY</a>
    <a style="left:837px" href="#">CONTACT</a>
    <span class="underline"></span>
  </nav>
  <div class="abs brand">
    <span class="mark"></span>
    <span class="name">NORTHLANE<br>INTERIORS</span>
  </div>
</header>

<section class="abs call">
  <span>CALL US KNOW</span>
  <svg class="icon" viewBox="0 0 76 76" aria-hidden="true">
    <circle cx="38" cy="38" r="35" fill="none" stroke="#111" stroke-width="3"/>
    <path d="M26 24c3-3 6-2 7 0l3 6c1 2 0 3-2 5 2 4 5 7 9 9 2-2 3-3 5-2l6 3c2 1 3 4 0 7-4 4-10 3-18-5s-13-17-10-23z" fill="#111"/>
    <path d="M42 22a12 12 0 0 1 12 12M42 28a6 6 0 0 1 6 6" fill="none" stroke="#111" stroke-width="2.5" stroke-linecap="round"/>
  </svg>
  <span>+1 555 010 2030</span>
</section>

<section>
  <h2 class="abs section-title" style="top:858px">ABOUT <span>NORTHLANE INTERIORS</span></h2>
  <p class="abs about-text">Lorem Ipsum is simply dummy text of the printing and typesetting industry. Lorem Ipsum has been the industry's standard dummy text ever since the 1500s, when an unknown printer took a galley of type and scrambled it to make a type specimen book. It has survived not only five centuries, but also the leap into electronic typesetting, Lorem Ipsum is simply dummy text of the printing and typesetting industry. Lorem Ipsum has been the industry's standard dummy text ever since the 1500s,</p>
  <a class="abs btn" style="left:506px;top:1042px;width:186px;height:60px">KNOW MORE</a>
</section>

<section>
  <div class="abs services"></div>
  <div class="abs shelf" role="img" aria-label="Photo of a wooden shelf with books, vases and plates against a white brick wall"></div>
  <h2 class="abs section-title" style="top:1224px">OUR <span>SERVICES</span></h2>

  <div class="abs svc-img" style="top:1296px;background:linear-gradient(135deg,#cfd4d8,#9ea4a8 50%,#8a6e4f)" role="img" aria-label="Photo of a modern commercial office interior with a curved reception desk"></div>
  <h3 class="abs svc-title" style="top:1298px">COMMERCIAL DESIGN</h3>
  <p class="abs svc-text" style="top:1330px">Lorem Ipsum is simply dummy text of the printing and typesetting industry. Lorem Ipsum has been the industry's standard dummy text ever since the 1500s, when an unknown printer took a galley of type and scrambled it to make e specimen book. It has survived not only five centuries...</p>
  <span class="abs read-more" style="top:1440px">READ MORE...<svg width="16" height="12" viewBox="0 0 16 12"><path d="M2 1l5 5-5 5M8 1l5 5-5 5" fill="none" stroke="currentColor" stroke-width="1.6"/></svg></span>

  <div class="abs svc-img" style="top:1477px;background:linear-gradient(135deg,#d9e86a,#c6d84f 50%,#e8ecd2)" role="img" aria-label="Photo of a residential living room with a lime patterned feature wall"></div>
  <h3 class="abs svc-title" style="top:1475px">RESIDENTIAL DESIGN</h3>
  <p class="abs svc-text" style="top:1508px">Lorem Ipsum is simply dummy text of the printing and typesetting industry. Lorem Ipsum has been the industry's standard dummy text ever since the 1500s, when an unknown printer took a galley of type and scrambled it to make e specimen book. It has survived not only five centuries...</p>
  <span class="abs read-more" style="top:1618px">READ MORE...<svg width="16" height="12" viewBox="0 0 16 12"><path d="M2 1l5 5-5 5M8 1l5 5-5 5" fill="none" stroke="currentColor" stroke-width="1.6"/></svg></span>
</section>

<section>
  <h2 class="abs section-title" style="top:1762px">OUR <span>GALLERY</span></h2>
  <span class="abs tab active" style="left:241px;width:256px">ALL INTERIORS DESIGNS</span>
  <span class="abs tab" style="left:515px;width:210px">COMMERCIAL DESIGN</span>
  <span class="abs tab" style="left:740px;width:212px">RESIDENTIAL DESIGN</span>
  <div class="abs gal-img" style="left:78px;background:linear-gradient(135deg,#3a1d14,#6b2e1e 50%,#8c5a6e)" role="img" aria-label="Photo of a dark red room with a pink lounge chair and lamp"></div>
  <div class="abs gal-img" style="left:343px;background:linear-gradient(135deg,#c7b77a,#a99a68 50%,#b5402c)" role="img" aria-label="Photo of a room with a wood panel feature wall and red chairs"></div>
  <div class="abs gal-img" style="left:607px;background:linear-gradient(135deg,#e6e3df,#cfcac4 55%,#a84a3c)" role="img" aria-label="Photo of an office corridor with a circle pattern wall film"></div>
  <div class="abs gal-img" style="left:873px;background:linear-gradient(135deg,#d9e86a,#c6d84f 50%,#e8ecd2)" role="img" aria-label="Photo of a living room with a lime patterned feature wall"></div>
  <a class="abs btn" style="left:506px;top:2098px;width:186px;height:60px">VIEW ALL</a>
</section>

<section class="abs newsletter">
  <h2>SUBSCRIBE TO OUR NEWSLETTER</h2>
</section>
<a class="abs subscribe">SUBSCRIBE NOW
  <svg width="30" height="28" viewBox="0 0 30 28" aria-hidden="true"><path d="M2 13L28 2 23 26 14 18 2 13zM14 18l-1 8 4-5M28 2L14 18" fill="none" stroke="currentColor" stroke-width="2" stroke-linejoin="round"/></svg>
</a>

<footer>
  <div class="abs footer"></div>
  <h4 class="abs foot-head" style="left:78px">USEFULL LINKS</h4>
  <ul class="abs foot-list" style="left:78px">
    <li>Home</li><li>About Us</li><li>Services</li><li>Gallery</li><li>Contact</li>
  </ul>
  <h4 class="abs foot-head" style="left:313px">OUR SERVICES</h4>
  <ul class="abs foot-list" style="left:313px">
    <li>Commercial Design</li><li>Residential Design</li>
  </ul>
  <h4 class="abs foot-head" style="left:580px">GET IN TOUCH</h4>
  <div class="abs contact-row" style="top:2428px">
    <svg width="20" height="22" viewBox="0 0 20 22"><path d="M9 1v20M3 4h13l3 3-3 3H3zM4 12h12v5H4z" fill="#1575d6"/></svg>
    <span>Lorem Ipsum is simple dummy text<br>of printing and type sretttin</span>
  </div>
  <div class="abs contact-row" style="top:2494px">
    <svg width="20" height="16" viewBox="0 0 20 16"><rect x="0" y="0" width="20" height="16" fill="#1575d6"/><path d="M1 1l9 8 9-8" fill="none" stroke="#2f2f2f" stroke-width="1.8"/></svg>
    <span>info@northlaneinteriors.com</span>
  </div>
  <div class="abs contact-row" style="top:2536px">
    <svg width="20" height="20" viewBox="0 0 20 20"><path d="M3 2c2-2 4-1 5 1l1 3c0 2-1 2-2 3 1 2 3 4 5 5 1-1 2-2 3-1l3 1c2 1 2 3 0 5-3 2-7 1-11-3S1 5 3 2z" fill="#1575d6"/></svg>
    <span>555 010 2030</span>
  </div>
  <div class="abs foot-brand">
    <span class="mark"></span>
    <span class="name">NORTHLANE<br>INTERIORS</span>
  </div>
  <div class="abs foot-rule"></div>
  <span class="abs social" style="left:927px;background:#1575d6"></span>
  <span class="abs social" style="left:978px;background:#8a8a8a"></span>
  <span class="abs social" style="left:1029px;background:#8a8a8a"></span>
  <p class="abs copyright">©<span>NorthlaneInteriors</span> - 2016. All rights reserved.</p>
</footer>

</body>
</html>
```